The Moss Hollow Organic & Natural Soaps is looking for label designs (along with the business card proje

This is my scope and requirements:
Labelling project:
This is related to the Label project I also opened up. (The Moss Hollow Organic & Natural Soaps needs a good business card (Contest) )
I have attached an initial draft at a logo I tried to come up with for a business card and labelling/marketing. I am hoping that you can take this logo and 'run with it' to finesse it, make it look unique and professional. If you need to change it, I am open to ideas.
I find that labelling/packaging is hard for me to make it look 'professional' so I am coming to the experts!
I am looking for label designs for 2 different bottles and 2 different bar soaps:
1) Organic Bar Soap (2 possibilities: 1) Kraft 'cigar' band around soap with twine, 2) Kraft soap box with Kraft sticker Labels
2) Natural Olive Oil Based Bar Soap (labelling can be same as Organic but with distinct info)
3) Organic Hand Washes (clear square bottles, 250ml with natural pump)
4) Natural Olive Oil Based Body Wash (taper bottle 200ml with metal silver disc top caps)
I am a start up at home company making Organic and Natural Bar soaps, hand soaps, body washes.
All of my ingredients are organic or natural and will include natural essential oils, exfoliants, natural powders/colours, etc.
Some of the names are: Bramblix (feisty, energetic soap), Dusk (more of a sandalwood earthy tones with a sandalwood powder exfoliant), Tidal (maybe changing this name - fresh scented), Plum Basil (lemongrass/ginger, exfoliants), etc....
If you need more information, please let me know!
Please find attached: Kraft Paper I am looking at to possibly wrap the Bar Soaps in (I like the different colour concept and am trying to decide between diff colours of Wren Mabry paper to wrap around or plain kraft paper.. whichever the new logo concept will look best with.
The bottles I will be using for the hand soap (250ml square) and the body wash (200ml tapered)
OLD POST:
Hello! I am a start up business that is specializing in making luxury organic bar soaps, natural olive oil bar soaps, organic hand wash, natural olive oil body wash/shower gel that will include essential oils, exfoliants, natural powders, etc. (also accessories: wood soap dishes, etc) .. I am looking for a great designer that can provide me with the business card and labelling designs! I appreciate feedback, ideas on how I can receive a great design to help sell my products!
I am attaching my initial logo design that I would like to keep - but am looking for someone to 'finesse' it or make it more professional/unique looking.
Again, this is hand in hand with the business card project I submitted.
Thanks!
Odile
Updates
I am sorry for the lack of direction or Scope of the project. I am new at this board.
Labelling project:
I have attached an initial draft at a logo I tried to come up with for a business card and labelling/marketing. I am hoping that you can take this logo and 'run with it' to finesse it, make it look unique and professional.
If you need more information, please let me know.
Hello; I just wanted to let everyone know that if you feel that this brand needs a different logo, I am open to ideas (if you don't think the one I started with is ok). I am coming to the experts here!
Just to confirm also - this is related to the business card project, therefore, there are 2 projects, 2 payments! :)
Cheers

```html
<!DOCTYPE html>
<html lang="en">
<head>
<meta charset="utf-8">
<title>The Moss Hollow – Dusk Organic Hand Wash Label</title>
<link rel="stylesheet" href="https://fonts.googleapis.com/css2?family=Crimson+Text:ital,wght@0,400;0,700;1,400&family=Lobster&display=swap">
<style>
  :root {
    --backdrop: #e4e4e4;
    --kraft: #c8a47a;
    --terracotta: #b55d4b;
    --band-orange: #d27f34;
    --band-tab: #8b4a22;
    --ink: #2b1a14;
    --cream: #f4e7cc;
    --pill: #2a1a16;
    --bracket: #5a2e24;
  }
  * { margin: 0; padding: 0; box-sizing: border-box; }
  html, body {
    width: 800px;
    height: 1200px;
    overflow: hidden;
    background: var(--backdrop);
  }
  .label {
    position: absolute;
    left: 120px;
    top: 45px;
    width: 560px;
    height: 1110px;
    background: var(--kraft);
  }
  .label-panel {
    position: absolute;
    left: 0;
    right: 0;
    top: 25px;
    bottom: 28px;
    background: var(--terracotta);
    color: var(--ink);
    font-family: "Crimson Text", Georgia, serif;
    text-align: center;
  }
  .brand {
    position: absolute;
    top: 80px;
    left: 0;
    right: 0;
    display: flex;
    align-items: center;
    justify-content: center;
    gap: 18px;
    color: var(--cream);
    font-weight: 700;
  }
  .brand-dot {
    width: 34px;
    height: 34px;
    border-radius: 50%;
    background: var(--cream);
    flex: none;
  }
  .brand-name {
    display: flex;
    flex-direction: column;
    line-height: 1.05;
  }
  .brand-main { font-size: 58px; }
  .brand-sub { font-size: 21px; letter-spacing: 2px; text-transform: uppercase; }
  .base-note {
    position: absolute;
    top: 276px;
    left: 0;
    right: 0;
    font-style: italic;
    font-size: 24px;
  }
  .divider {
    position: absolute;
    top: 349px;
    left: 50%;
    transform: translateX(-50%);
  }
  .scent-name {
    position: absolute;
    top: 384px;
    left: 0;
    right: 0;
    font-family: "Lobster", cursive;
    font-weight: 400;
    font-size: 54px;
    line-height: 1.1;
  }
  .scent-band {
    position: absolute;
    top: 470px;
    left: 0;
    right: 0;
    height: 155px;
    background: var(--band-orange);
    display: flex;
    align-items: center;
    justify-content: center;
  }
  .scent-band::before,
  .scent-band::after {
    content: "";
    position: absolute;
    top: 82px;
    width: 62px;
    height: 42px;
    background: var(--band-tab);
  }
  .scent-band::before { left: 0; }
  .scent-band::after { right: 0; }
  .scent-notes {
    font-size: 22px;
    line-height: 1.35;
  }
  .botanical {
    position: absolute;
    top: 700px;
    left: 130px;
    width: 312px;
    height: 110px;
    border-radius: 55px;
    background: radial-gradient(ellipse at center, rgba(198,69,47,0.55) 0%, rgba(123,138,85,0.35) 55%, rgba(181,93,75,0) 80%);
  }
  .product-type {
    position: absolute;
    top: 888px;
    left: 0;
    right: 0;
    font-weight: 700;
    font-size: 28px;
  }
  .type-bracket {
    position: absolute;
    top: 932px;
    left: 50%;
    transform: translateX(-50%);
  }
  .volume {
    position: absolute;
    top: 990px;
    left: 50%;
    transform: translateX(-50%);
    background: var(--pill);
    color: var(--cream);
    font-weight: 700;
    font-size: 20px;
    padding: 2px 14px;
    border-radius: 14px;
    white-space: nowrap;
  }
</style>
</head>
<body>
  <div class="label">
    <div class="label-panel">
      <div class="brand">
        <span class="brand-dot"></span>
        <div class="brand-name">
          <span class="brand-main">The Moss Hollow</span>
          <span class="brand-sub">Organic &amp; Natural Soaps</span>
        </div>
      </div>

      <p class="base-note">With Natural Oil Based</p>

      <svg class="divider" width="160" height="12" viewBox="0 0 160 12">
        <line x1="0" y1="6" x2="160" y2="6" stroke="#2b1a14" stroke-width="1.5"/>
        <polygon points="80,1 86,6 80,11 74,6" fill="#2b1a14"/>
      </svg>

      <h1 class="scent-name">Dusk</h1>

      <div class="scent-band">
        <p class="scent-notes">sandalwood earthy tones with<br>a sandalwood powder exfoliant</p>
      </div>

      <div class="botanical" role="img" aria-label="Sprig of red berries with slender green leaves"></div>

      <p class="product-type">Organic Hand Washes</p>

      <svg class="type-bracket" width="190" height="50" viewBox="0 0 190 50">
        <path d="M2 0 V48 H188 V0" fill="none" stroke="#5a2e24" stroke-width="1.2"/>
      </svg>

      <span class="volume">250 ml</span>
    </div>
  </div>
</body>
</html>
```